Logo, Web and Mobile Designs for enterprise social media platform

All the details are in the attached document, please start reading the scope document first which explains what is this project about and the details about the needed deliverables, after that please read the UI_Requirements document which will detail what is expected regarding the coded web version since this is a coded contest, it is very important that you meet the UI requirements or suggest something else but we will need to agree first before working on the coded version

Good Luck

Target Market(s)

Enterprise Social Media

Industry/Entity Type

Media

Coding

Coded - Design and coding required

Number of Pages Required

5+ page

Font styles to use
Sans Serif

Requirements
Must have
• All the must haves are listed in the scope document so please check before you start

```html
<!DOCTYPE html>
<html lang="en">
<head>
<meta charset="utf-8">
<title>Teamora – Sign In</title>
<link rel="stylesheet" href="https://fonts.googleapis.com/css2?family=Roboto:wght@400;500&family=Open+Sans:wght@400&family=Ubuntu:wght@500&display=swap">
<style>
  :root {
    --page-bg: #f1f1f1;
    --header-bg: #fbfbfb;
    --line: #e2e2e2;
    --text: #5a5a5a;
    --text-dark: #444;
    --brand-blue: #1e9ccf;
    --footer-blue: #1e8ab4;
    --accent-orange: #e88f00;
    --progress-orange: #ec5a1c;
    --white: #ffffff;
    --icon-grey: #a8a8a8;
  }
  * { box-sizing: border-box; margin: 0; padding: 0; }
  html, body { width: 1200px; height: 662px; overflow: hidden; }
  body {
    position: relative;
    background: linear-gradient(135deg, #f5f5f5 0%, #ececec 50%, #f4f4f4 100%);
    font-family: "Roboto", Arial, sans-serif;
    color: var(--text);
  }

  /* Header */
  .site-header {
    position: absolute; left: 0; top: 0; width: 1200px; height: 86px;
    background: var(--header-bg);
    border-bottom: 1px solid var(--line);
  }
  .brand {
    position: absolute; left: 99px; top: 25px;
    display: flex; align-items: center; gap: 8px;
  }
  .brand-dot { width: 34px; height: 34px; border-radius: 50%; background: var(--accent-orange); }
  .brand-name {
    font-family: "Ubuntu", "Roboto", sans-serif; font-weight: 500;
    font-size: 31px; color: var(--brand-blue); letter-spacing: .3px;
  }
  .main-nav { position: absolute; top: 37px; left: 0; }
  .main-nav a {
    position: absolute; font-size: 13.5px; color: var(--text-dark);
    text-decoration: none; white-space: nowrap; letter-spacing: .3px;
  }
  .main-nav .is-active::after {
    content: ""; position: absolute; left: -1px; right: -1px; top: 46px;
    height: 2px; background: var(--brand-blue);
  }

  /* Video */
  .video-player {
    position: absolute; left: 98px; top: 125px; width: 530px; height: 426px;
    box-shadow: 0 1px 3px rgba(0,0,0,.15);
  }
  .video-poster {
    width: 530px; height: 395px;
    background: linear-gradient(160deg, #9a8878 0%, #b89a86 30%, #6f6a70 55%, #27303f 75%, #d9d2cb 100%);
  }
  .video-play {
    position: absolute; left: 238px; top: 184px; width: 54px; height: 54px;
  }
  .video-controls {
    position: absolute; left: 0; top: 395px; width: 530px; height: 31px;
    background: linear-gradient(#fafafa, #ececec);
    border-top: 1px solid #ddd;
  }
  .video-controls .time {
    position: absolute; left: 52px; top: 10px; font-size: 7.5px; color: #333;
  }
  .progress { position: absolute; left: 126px; top: 14px; width: 210px; height: 3px; background: #444; border-radius: 2px; }
  .progress span { display: block; width: 97px; height: 3px; background: var(--progress-orange); border-radius: 2px; }
  .volume { position: absolute; left: 476px; top: 14px; width: 40px; height: 3px; background: #444; border-radius: 2px; }
  .volume span { display: block; width: 30px; height: 3px; background: var(--progress-orange); border-radius: 2px; }

  /* Auth panel */
  .auth-panel {
    position: absolute; left: 647px; top: 125px; width: 454px; height: 426px;
    background: rgba(255,255,255,.55); border: 1px solid var(--line);
  }
  .panel-title {
    position: absolute; left: 17px; font-weight: 500; font-size: 19px;
    color: var(--text); letter-spacing: .6px;
  }
  .divider { position: absolute; left: 0; width: 452px; height: 1px; background: var(--line); }
  .field-label {
    position: absolute; font-size: 12.5px; color: var(--text); white-space: nowrap;
  }
  .field-label b { font-weight: 400; font-size: 10px; }
  .field {
    position: absolute; height: 39px; background: var(--white);
    border: 1px solid #e6e6e6; border-radius: 2px;
  }
  .field svg { position: absolute; right: 12px; top: 13px; }
  .remember {
    position: absolute; left: 103px; top: 202px; display: flex; align-items: center; gap: 5px;
    font-family: "Open Sans", Arial, sans-serif; font-size: 12.5px; color: var(--text);
  }
  .remember i { width: 13px; height: 13px; border: 1px solid #555; border-radius: 50%; display: block; }
  .forgot {
    position: absolute; left: 224px; top: 202px;
    font-family: "Open Sans", Arial, sans-serif; font-size: 12.5px; color: var(--text);
    text-decoration: underline;
  }
  .btn {
    position: absolute; color: var(--white); font-size: 13px; border-radius: 3px;
    display: flex; align-items: center; justify-content: center; letter-spacing: .3px;
  }
  .btn-signin { left: 329px; top: 194px; width: 97px; height: 33px; background: var(--accent-orange); }
  .btn-register { left: 323px; top: 381px; width: 105px; height: 34px; background: var(--brand-blue); }

  /* Footer */
  .site-footer {
    position: absolute; left: 0; top: 593px; width: 1200px; height: 69px;
    background: var(--footer-blue); color: var(--white); font-size: 13px;
  }
  .site-footer span { position: absolute; top: 28px; white-space: nowrap; }
</style>
</head>
<body>
  <header class="site-header">
    <div class="brand"><span class="brand-dot"></span><span class="brand-name">Teamora</span></div>
    <nav class="main-nav">
      <a class="is-active" style="left:879px">HOME</a>
      <a style="left:959px">ABOUT US</a>
      <a style="left:1064px">NEWS</a>
    </nav>
  </header>

  <section class="video-player">
    <div class="video-poster" role="img" aria-label="Photo of a speaker at a laptop presenting to a conference audience"></div>
    <svg class="video-play" viewBox="0 0 54 54">
      <circle cx="27" cy="27" r="25" fill="#3a3a3a" stroke="#f2f2f2" stroke-width="3"/>
      <path d="M21 16 L38 27 L21 38 Z" fill="#ffffff"/>
    </svg>
    <div class="video-controls">
      <svg style="position:absolute;left:18px;top:11px" width="8" height="9" viewBox="0 0 8 9"><path d="M0 0L8 4.5L0 9Z" fill="#222"/></svg>
      <span class="time">10:00/05:03</span>
      <div class="progress"><span></span></div>
      <svg style="position:absolute;left:457px;top:10px" width="14" height="11" viewBox="0 0 14 11"><path d="M0 3.5H3L7 0V11L3 7.5H0Z" fill="#222"/><path d="M9 3Q11 5.5 9 8M11 1.5Q14 5.5 11 9.5" stroke="#222" fill="none"/></svg>
      <div class="volume"><span></span></div>
    </div>
  </section>

  <section class="auth-panel">
    <h2 class="panel-title" style="top:23px">TEAMORA SIGN IN</h2>
    <div class="divider" style="top:60px"></div>

    <label class="field-label" style="left:18px;top:98px">User Name <b>*</b></label>
    <div class="field" style="left:103px;top:86px;width:323px">
      <svg width="12" height="13" viewBox="0 0 12 13"><circle cx="6" cy="3.5" r="3.2" fill="#a8a8a8"/><path d="M0 13Q0 7 6 7Q12 7 12 13Z" fill="#a8a8a8"/></svg>
    </div>

    <label class="field-label" style="left:27px;top:151px">Password <b>*</b></label>
    <div class="field" style="left:103px;top:139px;width:323px">
      <svg width="12" height="12" viewBox="0 0 12 12" fill="#a8a8a8"><circle cx="6" cy="1.2" r="1.2"/><circle cx="10.2" cy="3" r="1"/><circle cx="10.8" cy="6.8" r="1"/><circle cx="8.5" cy="10.4" r="1"/><circle cx="4" cy="10.6" r="1"/><circle cx="1.2" cy="7.4" r="1"/><circle cx="1.8" cy="3" r="1.1"/></svg>
    </div>

    <div class="remember"><i></i>Remember me</div>
    <a class="forgot">Forgot Password</a>
    <div class="btn btn-signin">SIGN IN</div>

    <div class="divider" style="top:251px"></div>
    <h2 class="panel-title" style="top:271px">TEAMORA SIGN UP</h2>
    <div class="divider" style="top:310px"></div>

    <label class="field-label" style="left:24px;top:346px">E - Mail <b>*</b></label>
    <div class="field" style="left:106px;top:330px;width:323px">
      <svg width="14" height="11" viewBox="0 0 14 11"><rect x=".5" y=".5" width="13" height="10" fill="none" stroke="#a8a8a8"/><path d="M.5 .5L7 6L13.5 .5" fill="none" stroke="#a8a8a8"/></svg>
    </div>
    <div class="btn btn-register">REGISTER</div>
  </section>

  <footer class="site-footer">
    <span style="left:99px">Terms &amp; Conditions</span>
    <span style="left:423px">Copyright @ 2015 - 2015.Teamora. All Rights Reserved.</span>
    <span style="left:1022px">Privacy Policy</span>
  </footer>
</body>
</html>
```